Heron Loan Partners Business Card

We need a business card design for our mortgage servicing company. In addition to servicing the loans of homeowners, we help homeowners with purchasing their homes and any mortgage refinancing. We would like to see designs that use the colors in the logo attached below (gold-ish yellow and navy blue), and any other design you deem fit! The design should communicate a simpler life with smart mortgages provided by Heron.

```html
<!DOCTYPE html>
<html lang="en">
<head>
<meta charset="utf-8">
<title>Heron Loan Partners Business Card</title>
<link rel="stylesheet" href="https://fonts.googleapis.com/css2?family=Arimo:wght@400;700&display=swap">
<style>
  :root {
    --backdrop: #55565a;
    --paper: #f7f7f5;
    --navy: #1f1b55;
    --navy-deep: #16133f;
    --gold: #d4a528;
    --gold-edge: #b8891a;
    --ink: #3a3a3f;
    --rule: #9a9aa2;
    --white: #ffffff;
  }
  * { margin: 0; padding: 0; box-sizing: border-box; }
  html, body {
    width: 1200px; height: 1108px; overflow: hidden;
    background: var(--backdrop);
    font-family: "Arimo", Arial, sans-serif;
  }
  .stage {
    position: relative; width: 1200px; height: 1108px;
    display: flex; flex-direction: column; align-items: center; justify-content: center; gap: 70px;
  }
  .card {
    position: relative; width: 720px; height: 412px;
    border-bottom: 5px solid var(--gold-edge);
  }
  .card-front { background: var(--paper); }
  .card-back { background: linear-gradient(180deg, var(--navy-deep), var(--navy)); }

  .brand {
    position: absolute; left: 0; right: 0; top: 92px;
    display: flex; align-items: center; justify-content: center; gap: 14px;
  }
  .brand-dot { width: 16px; height: 16px; border-radius: 50%; background: var(--gold); }
  .brand-name {
    font-weight: 700; font-size: 46px; letter-spacing: 0.5px; color: var(--gold);
  }
  .card-back .brand { top: 130px; }

  .identity {
    position: absolute; left: 40px; top: 262px; width: 290px; text-align: right;
    color: var(--ink);
  }
  .identity .person { font-weight: 700; font-size: 26px; color: var(--navy); }
  .identity .role { font-size: 15px; color: #77777d; margin-top: 2px; }
  .identity .address { font-size: 15px; line-height: 1.35; margin-top: 4px; }

  .divider {
    position: absolute; left: 352px; top: 262px; width: 1px; height: 120px; background: var(--rule);
  }

  .contacts {
    position: absolute; left: 376px; top: 272px; list-style: none;
    font-size: 16px; color: var(--ink);
  }
  .contacts li { display: flex; align-items: center; gap: 10px; height: 25px; }
  .contacts svg { width: 15px; height: 15px; flex: none; }

  .tagline {
    position: absolute; left: 0; right: 0; top: 270px; text-align: center;
    color: var(--white); font-size: 18px;
  }
</style>
</head>
<body>
<main class="stage">
  <section class="card card-front" aria-label="Business card front">
    <div class="brand">
      <span class="brand-dot"></span>
      <span class="brand-name">Heron Loan Partners</span>
    </div>
    <div class="identity">
      <p class="person">Daniel Reeve</p>
      <p class="role">President</p>
      <p class="address">412 Willow Bend Road<br>Fairview, Canada 48210</p>
    </div>
    <div class="divider"></div>
    <ul class="contacts">
      <li>
        <svg viewBox="0 0 16 16" aria-hidden="true"><path fill="#d4a528" d="M3.5 1.5l2.5 0 1 3.5-1.8 1.2c.8 1.8 2.2 3.2 4 4l1.2-1.8 3.5 1v2.5c0 .8-.7 1.5-1.5 1.5C6.8 13.4 2.6 9.2 2 3c0-.8.7-1.5 1.5-1.5z"/></svg>
        555-302-1187
      </li>
      <li>
        <svg viewBox="0 0 16 16" aria-hidden="true"><rect x="4" y="1" width="8" height="14" rx="1.5" fill="none" stroke="#d4a528" stroke-width="1.6"/><circle cx="8" cy="12.5" r="0.9" fill="#d4a528"/></svg>
        555-914-6620
      </li>
      <li>
        <svg viewBox="0 0 16 16" aria-hidden="true"><rect x="1.5" y="3.5" width="13" height="9" fill="#d4a528"/><path d="M1.5 3.5l6.5 5 6.5-5" fill="none" stroke="#f7f7f5" stroke-width="1.2"/></svg>
        hello@heronloanpartners.com
      </li>
      <li>
        <svg viewBox="0 0 16 16" aria-hidden="true"><circle cx="8" cy="8" r="6.5" fill="#d4a528"/><path d="M1.5 8h13M8 1.5c-2.4 2.4-2.4 10.6 0 13M8 1.5c2.4 2.4 2.4 10.6 0 13" fill="none" stroke="#f7f7f5" stroke-width="0.9"/></svg>
        www.heronloanpartners.com
      </li>
    </ul>
  </section>

  <section class="card card-back" aria-label="Business card back">
    <div class="brand">
      <span class="brand-dot"></span>
      <span class="brand-name">Heron Loan Partners</span>
    </div>
    <p class="tagline">Simpler life with smart mortgages</p>
  </section>
</main>
</body>
</html>
```